Emerging automotive detailing business

I am starting a small automotive detailing business in hopes of becoming a well-known detailer to work on high end cars. I would like a card to reflect the high quality and time I put into my work. The name of the company is Bright Crest Detailing. I feel like it represents racecars getting off the line at the drag strip as well as an innuendo of "Up the Ladder". I do minor paint correction such as clay barring, multi-step buffing and polishing, waxing, hand washes, etc. I am always striving to learn more and improve my work. My goal is to have total customer satisfaction. This is a female run business but I do not want it to be very girly. Elegant is okay! I have pictures of my personal wrenfield attached, they do not need to be incorporated but if you can think of a cool way to use 1 or all of them, go for it!

Target Market(s)

Anyone that owns a vehicle. Preferably high end vehicles such as Valtori, Castellverde and Morvani but I will also happily work on any car, truck or suv no matter what brand.

Industry/Entity Type

Automotive

Contact Information for Business Card

Bright Crest Detailing
Mira Tolland
4175 Quenhollow Rd
Ashmere PA 17492
Cell phone- call/text- 717-555-0148
email- brightcrestdetails@maildrop-example.com
Instagram: @brightcrestdetailing
Facebook: facebook.com/brightcrestdetailing

Requirements
Must have
• Business name, my name, address, phone number. Listing that I do minor paint correction such as clay barring, multi-step buffing and polishing, waxing, hand washes, interior cleaning, and more. (This last part was in nice to haves but I have realized that I do really want it, so I moved it to must haves.) I want something that is different and eye-catching to my customers. Some people have done this very well with cards already submitted to me, but a lot have not. I didn't mess with the "look and feel bars" much because because I am pretty open to the overall design as long as it is not your basic run of the mill design.
Nice to have
• Something car related. Maybe an appointment time/date line. I do not have a logo, but if you would like to design one and incorporate it, that would be amazing!
Should not have
• Purple and Pink colors. Boring, basic, normal card.

```html
<!DOCTYPE html>
<html lang="en">
<head>
<meta charset="utf-8">
<title>Bright Crest Detailing – Business Card</title>
<link href="https://fonts.googleapis.com/css2?family=Open+Sans:wght@300;400;600;700&display=swap" rel="stylesheet">
<style>
  :root {
    --backdrop: #161616;
    --card-blue-top: #0c74bf;
    --card-blue-bottom: #0e4a93;
    --accent-orange: #f7a823;
    --accent-orange-deep: #f08a1c;
    --ink-white: #ffffff;
    --ink-soft: #dce9f7;
    --ink-blue: #1458a8;
    --paper: #ffffff;
  }
  * { box-sizing: border-box; margin: 0; padding: 0; }
  html, body { width: 1200px; height: 900px; overflow: hidden; }
  body {
    background: var(--backdrop);
    font-family: "Open Sans", Arial, sans-serif;
    position: relative;
  }
  .card {
    position: absolute;
    top: 170px;
    width: 347px;
    height: 561px;
    overflow: hidden;
  }
  /* Front */
  .card-front {
    left: 259px;
    background: linear-gradient(to bottom, var(--card-blue-top), var(--card-blue-bottom));
    color: var(--ink-white);
    text-align: center;
  }
  .accent-tab {
    position: absolute;
    left: 102px;
    width: 143px;
    height: 30px;
    background: linear-gradient(to bottom, var(--accent-orange), var(--accent-orange-deep));
  }
  .accent-tab.top { top: 0; }
  .accent-tab.bottom { bottom: 0; }
  .brand-front {
    position: absolute;
    top: 138px;
    left: 0;
    width: 100%;
    font-weight: 600;
    line-height: 1.15;
  }
  .brand-front .brand-name { display: block; font-size: 38px; }
  .brand-front .brand-sub { display: block; font-size: 26px; letter-spacing: 10px; margin-top: 12px; font-weight: 600; }
  .holder-name {
    position: absolute;
    top: 286px;
    width: 100%;
    font-size: 21px;
    font-weight: 700;
    letter-spacing: 0.5px;
  }
  .address {
    position: absolute;
    top: 324px;
    width: 100%;
    font-size: 15px;
    line-height: 23px;
  }
  .contacts {
    position: absolute;
    top: 385px;
    width: 100%;
    list-style: none;
    font-size: 14.5px;
    line-height: 23px;
  }
  .contacts li { display: flex; justify-content: center; align-items: center; gap: 7px; }
  .contacts svg { width: 11px; height: 11px; fill: var(--ink-white); flex: none; }
  .contacts .email { font-size: 12.5px; }
  .services {
    position: absolute;
    top: 468px;
    left: 30px;
    width: 287px;
    font-size: 11px;
    line-height: 16px;
    color: var(--ink-soft);
  }

  /* Back */
  .card-back { left: 631px; background: var(--paper); }
  .back-rotated {
    position: absolute;
    left: -107px;
    top: 107px;
    width: 561px;
    height: 347px;
    transform: rotate(-90deg);
    color: var(--ink-blue);
  }
  .brand-back {
    position: absolute;
    left: 140px;
    top: 62px;
    width: 300px;
    font-weight: 600;
    line-height: 1.1;
  }
  .brand-back .brand-name { display: block; font-size: 38px; }
  .brand-back .brand-sub { display: block; font-size: 30px; letter-spacing: 12px; margin-top: 6px; font-weight: 600; }
  .appointment-title {
    position: absolute;
    left: 153px;
    top: 194px;
    font-size: 19px;
    font-weight: 700;
    white-space: nowrap;
  }
  .appointment-row {
    position: absolute;
    left: 93px;
    width: 373px;
    display: flex;
    align-items: flex-end;
    font-size: 13px;
    font-weight: 700;
    gap: 4px;
  }
  .appointment-row.date { top: 240px; }
  .appointment-row.time { top: 279px; }
  .fill-line {
    flex: 1;
    border-bottom: 1.5px dotted var(--ink-blue);
    margin-bottom: 4px;
    height: 1px;
  }
  .appointment-row .label { width: 46px; }
</style>
</head>
<body>

<section class="card card-front" aria-label="Business card front">
  <div class="accent-tab top"></div>
  <h1 class="brand-front">
    <span class="brand-name">Bright Crest</span>
    <span class="brand-sub">Detailing</span>
  </h1>
  <p class="holder-name">MIRA TOLLAND</p>
  <p class="address">4175 Quenhollow Rd<br>Ashmere PA 17492</p>
  <ul class="contacts">
    <li>
      <svg viewBox="0 0 24 24" aria-hidden="true"><path d="M6.6 10.8a15.1 15.1 0 0 0 6.6 6.6l2.2-2.2a1 1 0 0 1 1-.25 11.4 11.4 0 0 0 3.6.57 1 1 0 0 1 1 1V20a1 1 0 0 1-1 1A17 17 0 0 1 3 4a1 1 0 0 1 1-1h3.5a1 1 0 0 1 1 1c0 1.25.2 2.45.57 3.57a1 1 0 0 1-.25 1z"/></svg>
      <span>call/text- 717-555-0148</span>
    </li>
    <li class="email">
      <svg viewBox="0 0 24 24" aria-hidden="true"><path d="M2 5h20v14H2z M3.5 6.5 12 13l8.5-6.5" fill="none" stroke="#fff" stroke-width="2"/></svg>
      <span>brightcrestdetails@maildrop-example.com</span>
    </li>
    <li>
      <svg viewBox="0 0 24 24" aria-hidden="true"><rect x="3" y="3" width="18" height="18" rx="2"/></svg>
      <span>@brightcrestdetailing</span>
    </li>
  </ul>
  <p class="services">Minor paint correction: clay barring · multi-step buffing &amp; polishing · waxing · hand washes · interior cleaning &amp; more</p>
  <div class="accent-tab bottom"></div>
</section>

<section class="card card-back" aria-label="Business card back">
  <div class="back-rotated">
    <h2 class="brand-back">
      <span class="brand-name">Bright Crest</span>
      <span class="brand-sub">Detailing</span>
    </h2>
    <p class="appointment-title">Your Next Appointment is</p>
    <div class="appointment-row date">
      <span class="label">Date :</span>
      <span class="fill-line"></span>
    </div>
    <div class="appointment-row time">
      <span class="label">Time:</span>
      <span class="fill-line"></span>
      <span>AM</span>
      <span class="fill-line"></span>
      <span>PM</span>
    </div>
  </div>
</section>

</body>
</html>
```